College presentation for a Venture ForgeLab - how to talk to customers

I need a simple design for a college PowerPoint/ google slide presentation for students that are going through a Venture ForgeLab. No flashy colors
- Accessible font - or provide the font - I like the orvel's website font or normal text font
- use a neutral colors schemes of grays - with 1-2 highlight colors
- You can use the photos in the presentation or others
- Urgent the presentation is on Thursday - I will award the winner on Wednesday.
- It's 23 slides long.

Target Market(s)

College students interested in startups

Industry/Entity Type

College

Font styles to use
Serif
Sans Serif
Other font styles liked:
• helvetica

Colors

Designer to choose only greyscale colors for use in the design.

Requirements
Must have
• clean , simple design neural colors like greyscale with 1-3 pop colors
Should not have
• no flashy colors, or hard to read text

```html
<!DOCTYPE html>
<html lang="en">
<head>
<meta charset="utf-8">
<title>Customer Development – Mom's test</title>
<link href="https://fonts.googleapis.com/css2?family=Poppins:wght@300;400;500;600;700;800&display=swap" rel="stylesheet">
<style>
:root{
  --backdrop:#a7a7a7;
  --blue:#1565c0;
  --blue-deep:#1259b0;
  --blue-bright:#1e88e5;
  --ink:#1f1f1f;
  --text:#555;
  --muted:#777;
  --line:#cfcfcf;
  --floor:#ececec;
  --bubble:#e6e6e6;
  --white:#fff;
  --bevel:#8f8f8f;
}
*{box-sizing:border-box;margin:0;padding:0}
html,body{width:1200px;height:3981px;overflow:hidden}
body{position:relative;background:var(--backdrop);font-family:"Poppins",Helvetica,Arial,sans-serif;color:var(--ink)}
.backdrop{position:absolute;inset:0}
.slide{position:absolute;left:99px;width:1002px;height:563px;background:var(--white);overflow:hidden}
.slide--framed{border-top:9px solid var(--blue-bright);border-bottom:12px solid var(--blue-bright);box-shadow:inset -9px 0 0 var(--bevel)}
.notch{position:absolute;left:461px;top:0;width:80px;height:40px;border-radius:0 0 40px 40px;background:var(--blue);z-index:5}
.footer{position:absolute;left:32px;right:32px;bottom:18px;display:flex;justify-content:space-between;font-size:8px;color:var(--ink);z-index:4}
.photo{position:absolute}

/* cover */
.cover{top:97px;height:565px}
.cover__photo{left:0;top:0;width:1002px;height:480px;background:linear-gradient(180deg,#3a3a3a 0%,#6b6b6b 45%,#bdbdbd 78%,#fff 100%)}
.cover__title{position:absolute;right:521px;top:448px;text-align:right;font-weight:700;font-size:40px;line-height:42px;color:var(--blue);letter-spacing:.5px}
.cover__rule{position:absolute;left:499px;top:452px;width:3px;height:92px;background:var(--blue)}
.cover__subtitle{position:absolute;left:520px;top:446px;font-weight:300;font-size:39px;line-height:44px;color:var(--ink)}

/* mom's test overview */
.overview{top:742px}
.section-title{position:absolute;left:0;right:0;text-align:center;font-weight:700;color:var(--blue);font-size:40px}
.overview .section-title{top:50px}
.overview__diamond{position:absolute;left:347px;top:164px;z-index:1}
.topic{position:absolute;width:372px;height:150px;background:var(--white);box-shadow:0 2px 8px rgba(0,0,0,.18);padding:22px 18px 0 62px;z-index:2}
.topic__num{position:absolute;left:18px;top:14px;font-size:46px;font-weight:700;color:var(--blue);line-height:1}
.topic__title{font-size:17px;font-weight:600;color:var(--blue);margin-bottom:8px}
.topic__body{font-size:10px;line-height:18px;color:var(--text)}

/* customer development */
.stages{top:1384px}
.stages .section-title{top:70px}
.stage{position:absolute;top:173px;width:211px;height:299px;border:4px solid var(--blue-bright);border-radius:6px;padding:18px 22px 0}
.stage--deep{border-color:var(--blue-deep)}
.stage__icon{width:52px;height:52px;display:block;margin-bottom:12px}
.stage__title{font-size:20px;font-weight:600;line-height:26px;color:var(--ink);margin-bottom:14px}
.stage__item{font-size:13px;color:var(--text);padding:10px 0 12px;border-bottom:1px solid var(--line)}
.stage__item:first-of-type{padding-top:0}

/* people try to be nice */
.nice{top:2026px}
.nice__band{position:absolute;left:611px;top:0;width:391px;height:90px;background:var(--blue)}
.nice__accent{position:absolute;left:513px;top:301px;width:136px;height:203px;background:var(--blue-bright)}
.nice__photo{left:527px;top:86px;width:427px;height:401px;border-radius:8px;background:linear-gradient(135deg,#d9d9d9,#8a8a8a 60%,#5c5c5c)}
.nice__copy{position:absolute;left:62px;top:72px;width:430px}
.nice__title{font-size:38px;font-weight:700;color:var(--blue);line-height:46px;margin-bottom:14px}
.nice__lead{font-size:12px;font-weight:600;margin-bottom:12px}
.nice__claim{font-size:25px;font-weight:600;margin-bottom:12px}
.nice__eg{font-size:13px;margin-bottom:20px}
.nice__eg em{font-weight:300}
.nice__label{font-size:12px;font-weight:700;margin-bottom:8px}
.nice__para{font-size:10.2px;line-height:18.6px;color:var(--text);text-align:justify}

/* dialogue slides */
.dialogue--say{top:2669px}
.dialogue--think{top:3321px}
.dialogue__floor{position:absolute;left:0;right:0;top:366px;bottom:0;background:var(--floor)}
.dialogue__title{position:absolute;left:40px;top:28px;font-size:33px;font-weight:700;line-height:33px;color:var(--blue-deep)}
.dialogue__title span{display:block;color:var(--blue-bright)}
.dialogue__man{left:315px;top:107px;width:159px;height:433px;border-radius:70px 70px 10px 10px;background:linear-gradient(180deg,#bfbfbf,#5d5d5d);z-index:2}
.dialogue__woman{left:518px;top:146px;width:202px;height:354px;border-radius:80px 80px 10px 10px;background:linear-gradient(180deg,#d0d0d0,#6e6e6e);z-index:2}
.dialogue__art{position:absolute;left:0;top:0;z-index:1}
.bubble{position:absolute;transform:translate(-50%,-50%);font-size:8.5px;line-height:14px;color:var(--text);text-align:left;z-index:3}
.bubble b{color:var(--blue);font-weight:600}
.bubble i{font-style:normal;color:var(--blue-bright);display:block}
</style>
</head>
<body>

<svg class="backdrop" width="1200" height="3981" aria-hidden="true">
  <polygon points="1200,1105 1200,3981 711,3981 0,3247 0,2381" fill="#1259b0"/>
</svg>

<!-- Cover -->
<section class="slide cover">
  <div class="photo cover__photo" role="img" aria-label="Black and white photo of four students sitting on bean bags working on laptops"></div>
  <h1 class="cover__title">CUSTOMER<br>DEVELOPMENT</h1>
  <div class="cover__rule"></div>
  <p class="cover__subtitle">Mom’s test -<br>how to talk to customers</p>
</section>

<!-- Overview -->
<section class="slide slide--framed overview">
  <div class="notch"></div>
  <h2 class="section-title">Mom’s test:</h2>
  <svg class="overview__diamond" width="310" height="312" viewBox="0 0 310 312">
    <polygon points="18,156 52,124 86,156 52,188" fill="#1e88e5"/>
    <polygon points="224,156 258,124 292,156 258,188" fill="#1e88e5"/>
    <polygon points="155,0 311,156 155,312 -1,156" fill="#1e88e5"/>
    <polygon points="155,20 291,156 155,292 19,156" fill="#6b6b6b" role="img" aria-label="Photo of two young men looking at a laptop"/>
  </svg>
  <div class="topic" style="left:49px;top:139px">
    <span class="topic__num">1</span>
    <h3 class="topic__title">What is the problem?</h3>
    <p class="topic__body">Lorem ipsum dolor sit amet, consectetur adipiscing elit, sed do eius mod tempor incididunt ut labore et dolore magna aliqua. Ut enim ad minim veniam, quis nostrud exercitation ullamco laboris</p>
  </div>
  <div class="topic" style="left:583px;top:139px">
    <span class="topic__num">3</span>
    <h3 class="topic__title">How to ask questions?</h3>
    <p class="topic__body">Lorem ipsum dolor sit amet, consectetur adipiscing elit, sed do eius mod tempor incididunt ut labore et dolore magna aliqua. Ut enim ad minim veniam, quis nostrud exercitation ullamco laboris</p>
  </div>
  <div class="topic" style="left:49px;top:342px">
    <span class="topic__num">2</span>
    <h3 class="topic__title">How to talk to customers ?</h3>
    <p class="topic__body">Lorem ipsum dolor sit amet, consectetur adipiscing elit, sed do eius mod tempor incididunt ut labore et dolore magna aliqua. Ut enim ad minim veniam, quis nostrud exercitation ullamco laboris</p>
  </div>
  <div class="topic" style="left:583px;top:342px">
    <span class="topic__num">4</span>
    <h3 class="topic__title">Who to talk to?</h3>
    <p class="topic__body">Lorem ipsum dolor sit amet, consectetur adipiscing elit, sed do eius mod tempor incididunt ut labore et dolore magna aliqua. Ut enim ad minim veniam, quis nostrud exercitation ullamco laboris</p>
  </div>
  <div class="footer"><span>© 2022 Company name | All Rights Reserved</span><span>PAGE | 02</span></div>
</section>

<!-- Customer development stages -->
<section class="slide slide--framed stages">
  <div class="notch"></div>
  <h2 class="section-title">Customer Development</h2>
  <div class="stage" style="left:62px">
    <svg class="stage__icon" viewBox="0 0 52 52" fill="none" stroke="#1565c0" stroke-width="2">
      <circle cx="14" cy="8" r="4"/><circle cx="26" cy="8" r="4"/><circle cx="38" cy="8" r="4"/>
      <path d="M8 22v-4a6 6 0 0 1 12 0v4M20 22v-4a6 6 0 0 1 12 0v4M32 22v-4a6 6 0 0 1 12 0v4"/>
      <path d="M4 34l10-4h14l-2 6H16M4 44l8-4h18l14-10"/>
    </svg>
    <h3 class="stage__title">Customer<br>Discovery</h3>
    <p class="stage__item">Problem solution fit</p>
    <p class="stage__item">Proposed MVP</p>
    <p class="stage__item" style="border-bottom:0">Proposed Funnel(s)</p>
  </div>
  <div class="stage" style="left:279px">
    <svg class="stage__icon" viewBox="0 0 52 52" fill="none" stroke="#1565c0" stroke-width="2">
      <rect x="3" y="6" width="40" height="30"/><path d="M3 40h40M23 36v6"/>
      <path d="M10 30v-8M16 30v-12M22 30v-6"/><circle cx="34" cy="24" r="7"/><path d="M39 29l8 8"/>
      <path d="M9 16l8-6 6 4 10-6"/>
    </svg>
    <h3 class="stage__title">Customer<br>Validation</h3>
    <p class="stage__item">Product Market Fit</p>
    <p class="stage__item">Buisness Model</p>
    <p class="stage__item" style="border-bottom:0">Sales &amp; Marketing</p>
  </div>
  <div class="stage stage--deep" style="left:511px">
    <svg class="stage__icon" viewBox="0 0 52 52" fill="none" stroke="#1565c0" stroke-width="2">
      <path d="M2 18l10-8 8 4M50 18l-10-8-12 6-6 6 4 4 8-6"/>
      <path d="M8 22l14 14a3 3 0 0 0 4-4M14 28l12 10a3 3 0 0 0 4-4M20 32l8 6a3 3 0 0 0 4-4l-10-10M42 22L30 34"/>
    </svg>
    <h3 class="stage__title">Customer<br>Creation</h3>
    <p class="stage__item">Scale Execution</p>
  </div>
  <div class="stage stage--deep" style="left:725px">
    <svg class="stage__icon" viewBox="0 0 52 52" fill="none" stroke="#1565c0" stroke-width="2">
      <rect x="8" y="6" width="30" height="42"/><path d="M4 48h44M20 6V2h6v4"/>
      <rect x="13" y="12" width="5" height="5"/><rect x="21" y="12" width="5" height="5"/><rect x="29" y="12" width="5" height="5"/>
      <rect x="13" y="22" width="5" height="5"/><rect x="21" y="22" width="5" height="5"/><rect x="29" y="22" width="5" height="5"/>
      <rect x="13" y="32" width="5" height="5"/><rect x="29" y="32" width="5" height="5"/><path d="M21 48V38h5v10"/>
    </svg>
    <h3 class="stage__title">Company<br>Building</h3>
    <p class="stage__item">Scale Organization</p>
    <p class="stage__item">Scale Oprations</p>
  </div>
  <div class="footer"><span>© 2022 Company name | All Rights Reserved</span><span>PAGE | 03</span></div>
</section>

<!-- People try to be nice -->
<section class="slide slide--framed nice">
  <div class="nice__band"></div>
  <div class="notch"></div>
  <div class="nice__accent"></div>
  <div class="photo nice__photo" role="img" aria-label="Black and white photo of a young man with glasses working on a laptop"></div>
  <div class="nice__copy">
    <h2 class="nice__title">People try to be nice</h2>
    <p class="nice__lead">Therefore they lie in your face without realizing it</p>
    <p class="nice__claim">Bad data it worse than no data</p>
    <p class="nice__eg"><strong>E.g.</strong> <em>“I’ll definitely buy that”</em></p>
    <p class="nice__label">THE PROBLEM</p>
    <p class="nice__para">Lorem ipsum dolor sit amet, consectetur adipiscing elit, sed do eiusmod tempor incididunt ut labore et dolore magna aliqua. Ut enim ad minim veniam, quis nostrud exercitation ullamco laboris nisi ut aliquip ex ea commodo consequat. Duis aute irure dolor in reprehenderit in voluptate velit esse cillum dolore eu fugiat nulla pariatur. Excepteur sint occaecat cupidatat non proident, sunt in culpa qui officia deserunt mollit anim id est laborum.Lorem ipsum dolor sit amet, consectetur adipiscing elit, sed do eiusmod tempor incididunt ut labore et dolore magna aliqua. Ut enim ad minim veniam, quis nostrud exercitation ullamco laboris nisi ut aliquip ex ea commodo consequat. Duis aute irure dolor in reprehenderit in voluptate velit esse cillum dolore eu fugiat nulla pariatur. Excepteur sint occaecat cupidatat non proident, sunt in culpa qui officia deserunt mollit anim id est laborum.</p>
  </div>
  <div class="footer"><span>© 2022 Company name | All Rights Reserved</span><span>PAGE | 04</span></div>
</section>

<!-- What people say -->
<section class="slide slide--framed dialogue dialogue--say">
  <div class="dialogue__floor"></div>
  <div class="notch"></div>
  <h2 class="dialogue__title">Mom’s test -<span>What people say</span></h2>
  <svg class="dialogue__art" width="1002" height="542" aria-hidden="true">
    <polygon points="278,208 292,200 315,238" fill="#1e88e5"/>
    <polygon points="258,318 266,332 306,339" fill="#1e88e5"/>
    <polygon points="306,420 300,436 352,416" fill="#1e88e5"/>
    <polygon points="772,196 784,208 726,238" fill="#1e88e5"/>
    <polygon points="790,320 794,334 732,331" fill="#1e88e5"/>
    <polygon points="730,410 740,424 689,416" fill="#1e88e5"/>
    <ellipse cx="229" cy="176" rx="74" ry="50" fill="#e6e6e6"/>
    <ellipse cx="198" cy="308" rx="78" ry="50" fill="#e6e6e6"/>
    <ellipse cx="244" cy="436" rx="80" ry="58" fill="#e6e6e6"/>
    <ellipse cx="826" cy="164" rx="74" ry="48" fill="#e6e6e6"/>
    <ellipse cx="841" cy="294" rx="78" ry="48" fill="#e6e6e6"/>
    <ellipse cx="813" cy="444" rx="99" ry="68" fill="#e6e6e6"/>
  </svg>
  <div class="photo dialogue__man" role="img" aria-label="Black and white photo of a bearded man in a blazer sitting"></div>
  <div class="photo dialogue__woman" role="img" aria-label="Black and white photo of a woman in a striped dress sitting and gesturing"></div>
  <p class="bubble" style="left:229px;top:176px;width:100px"><b>You:</b> Mom, I have a business idea. Do you have 5 mins?</p>
  <p class="bubble" style="left:198px;top:308px;width:110px"><b>You:</b> You like your Slatepad and use it a lot?</p>
  <p class="bubble" style="left:244px;top:436px;width:100px"><b>You:</b> Would you buy a cookbook app?</p>
  <p class="bubble" style="left:826px;top:164px;width:104px"><b>Mom:</b> Of course, dear</p>
  <p class="bubble" style="left:841px;top:294px;width:104px"><b>Mom:</b> Sure it's great.</p>
  <p class="bubble" style="left:813px;top:444px;width:150px"><b>Mom:</b> I love cookbooks, sounds nice. Does it come with vegan recipes? Or something special for Xmas?</p>
  <div class="footer"><span>© 2022 Company name | All Rights Reserved</span><span>PAGE | 05</span></div>
</section>

<!-- What people think -->
<section class="slide slide--framed dialogue dialogue--think">
  <div class="dialogue__floor"></div>
  <div class="notch"></div>
  <h2 class="dialogue__title">Mom’s test -<span>What people think</span></h2>
  <svg class="dialogue__art" width="1002" height="542" aria-hidden="true">
    <polygon points="278,208 292,200 315,238" fill="#1e88e5"/>
    <polygon points="258,318 266,332 306,339" fill="#1e88e5"/>
    <polygon points="306,420 300,436 352,416" fill="#1e88e5"/>
    <polygon points="766,200 780,212 726,238" fill="#1e88e5"/>
    <polygon points="786,318 790,334 732,331" fill="#1e88e5"/>
    <polygon points="722,404 734,420 689,416" fill="#1e88e5"/>
    <ellipse cx="229" cy="176" rx="74" ry="50" fill="#e6e6e6"/>
    <ellipse cx="198" cy="308" rx="78" ry="50" fill="#e6e6e6"/>
    <ellipse cx="244" cy="436" rx="80" ry="58" fill="#e6e6e6"/>
    <ellipse cx="832" cy="164" rx="90" ry="60" fill="#e6e6e6"/>
    <ellipse cx="846" cy="296" rx="88" ry="62" fill="#e6e6e6"/>
    <ellipse cx="828" cy="451" rx="136" ry="104" fill="#e6e6e6"/>
  </svg>
  <div class="photo dialogue__man" role="img" aria-label="Black and white photo of a bearded man in a blazer sitting"></div>
  <div class="photo dialogue__woman" role="img" aria-label="Black and white photo of a woman in a striped dress sitting and gesturing"></div>
  <p class="bubble" style="left:229px;top:176px;width:100px"><b>You:</b> Mom, I have a business idea. Do you have 5 mins?</p>
  <p class="bubble" style="left:198px;top:308px;width:110px"><b>You:</b> You like your Slatepad and use it a lot?</p>
  <p class="bubble" style="left:244px;top:436px;width:100px"><b>You:</b> Would you buy a cookbook app?</p>
  <p class="bubble" style="left:832px;top:164px;width:140px"><b>Mom:</b> Of course, dear<i>I'm proud of you and I don't want to hurt your feelings</i></p>
  <p class="bubble" style="left:846px;top:296px;width:126px"><b>Mom:</b> Sure it's great.<i>I use it to check email on the sofa</i></p>
  <p class="bubble" style="left:828px;top:451px;width:170px"><b>Mom:</b> I love cookbooks, sounds nice. Does it come with vegan recipes? Or something special for Xmas?<i style="margin-top:6px">Well, I have plenty of cookbooks. I don't need a computer in my kitchen - it might get dirty!</i></p>
  <div class="footer"><span>© 2022 Company name | All Rights Reserved</span><span>PAGE | 06</span></div>
</section>

</body>
</html>
```